Marlow Estate Fixers (Handyman / Home Improvement Company)

Looking for a double sided professional looking business card with Logo attached to be highlighted on one side and throwing in an image of a handyman as an option would be nice to see as well. We are a company focused on providing quality Handyman and Home improvement services in a timely manner that is done right the first time with integrity

Industry/Entity Type

Handyman / Home Improvement

Contact Information for Business Card

(LOGO, Name, Mobile and office phone numbers, email) on front side of card, (the words "The SOLUTION to all of your Handyman and Home Improvement needs" followed by "Family Owned and Operated" at the very bottom) on the back.

Colors
EB3D1F
EC4F4E
F09395
F8D3D4
FCEDEE

Requirements
Must have
• Red, Gray, Black Color scheme
Should not have
• No Yellow or Blue colors

```html
<!DOCTYPE html>
<html lang="en">
<head>
<meta charset="utf-8">
<title>Marlow Estate Fixers – Business Card</title>
<link href="https://fonts.googleapis.com/css2?family=Russo+One&family=Poppins:wght@400&family=Crimson+Text:ital@1&display=swap" rel="stylesheet">
<style>
  :root {
    --red: #e8292d;
    --black: #050505;
    --white: #ffffff;
    --ink: #151515;
    --stage: #9a9a9a;
    --mint: #d3eccb;
    --rule: #d4d4d4;
  }
  * { box-sizing: border-box; margin: 0; padding: 0; }
  html, body { width: 1093px; height: 1200px; overflow: hidden; }
  body { background: var(--stage); position: relative; font-family: "Poppins", sans-serif; }

  .card {
    position: absolute;
    left: 264px;
    width: 580px;
    height: 357px;
    border-radius: 30px;
    overflow: hidden;
    box-shadow: 2px 4px 6px rgba(0,0,0,.35);
  }

  /* Front */
  .card--front { top: 226px; background: var(--white); }
  .card--front .base-band {
    position: absolute; left: 0; right: 0; bottom: 0; height: 12px; background: var(--red);
  }
  .brand {
    position: absolute; left: 38px; top: 150px; width: 232px;
    display: flex; align-items: center; gap: 10px;
  }
  .brand-mark { width: 22px; height: 22px; background: var(--red); flex: none; }
  .brand-name {
    font-family: "Russo One", sans-serif; font-size: 21px; line-height: 1.15;
    color: var(--black); text-transform: uppercase;
  }
  .divider {
    position: absolute; left: 289px; top: 97px; width: 1px; height: 162px; background: var(--rule);
  }
  .contact { position: absolute; left: 312px; top: 120px; }
  .contact-name {
    font-family: "Russo One", sans-serif; font-size: 22px; color: var(--red);
    letter-spacing: .3px; margin-bottom: 22px;
  }
  .contact-list { list-style: none; }
  .contact-list li {
    display: flex; align-items: center; gap: 8px;
    font-size: 17px; line-height: 22px; color: var(--ink);
  }
  .contact-list svg { width: 15px; height: 15px; flex: none; }

  /* Back */
  .card--back { top: 621px; width: 584px; background: var(--red); }
  .back-edge { position: absolute; right: 0; top: 0; bottom: 0; width: 140px; background: var(--black); }
  .mascot-art {
    position: absolute; left: 290px; top: 0; width: 270px; height: 357px;
    background: radial-gradient(circle 122px at 126px 120px, var(--mint) 99%, transparent 100%);
  }
  .tagline {
    position: absolute; left: 30px; top: 44px; width: 250px;
    font-family: "Russo One", sans-serif; color: var(--white); text-transform: uppercase;
    line-height: 1;
  }
  .tagline span { display: block; white-space: nowrap; }
  .tagline .t-sm { font-size: 25px; letter-spacing: 1.6px; margin-bottom: 6px; }
  .tagline .t-lg { font-size: 40px; letter-spacing: .3px; margin-top: 8px; }
  .tagline .t-xs { font-size: 19px; letter-spacing: .6px; margin-top: 0; }
  .family {
    position: absolute; left: 30px; top: 303px; display: flex; align-items: center; gap: 8px;
    font-family: "Crimson Text", serif; font-style: italic; font-size: 15px; color: var(--white);
  }
  .family::after { content: ""; width: 200px; height: 1px; background: rgba(255,255,255,.8); margin-top: 4px; }
</style>
</head>
<body>

<section class="card card--front" aria-label="Card front">
  <div class="brand">
    <span class="brand-mark"></span>
    <span class="brand-name">Marlow Estate Fixers</span>
  </div>
  <div class="divider"></div>
  <div class="contact">
    <p class="contact-name">DANIEL REEVE</p>
    <ul class="contact-list">
      <li>
        <svg viewBox="0 0 16 16" aria-hidden="true"><rect x="3.5" y="1" width="9" height="14" rx="1.5" fill="none" stroke="#e8292d" stroke-width="1.6"/><circle cx="8" cy="12.5" r=".9" fill="#e8292d"/></svg>
        044-555 210 378
      </li>
      <li>
        <svg viewBox="0 0 16 16" aria-hidden="true"><path d="M3 1.5l3 .5 1 3-1.8 1.3a8 8 0 0 0 4.5 4.5L11 9l3 1 .5 3-2 1.5C6.5 14 2 9.5 1.5 3.5z" fill="none" stroke="#e8292d" stroke-width="1.5" stroke-linejoin="round"/></svg>
        044-555 210 378
      </li>
      <li>
        <svg viewBox="0 0 16 16" aria-hidden="true"><rect x="1" y="3" width="14" height="10" fill="#e8292d"/><path d="M1 3l7 6 7-6" fill="none" stroke="#fff" stroke-width="1.2"/></svg>
        info@marlowfixers.com
      </li>
    </ul>
  </div>
  <div class="base-band"></div>
</section>

<section class="card card--back" aria-label="Card back">
  <div class="back-edge"></div>
  <div class="mascot-art" role="img" aria-label="Cartoon handyman in cap and overalls holding a cordless drill, in front of a pale mint circle"></div>
  <h1 class="tagline">
    <span class="t-sm">Your Solution</span>
    <span class="t-sm">To All of Your</span>
    <span class="t-lg">Handyman</span>
    <span class="t-lg">And Home</span>
    <span class="t-xs">Improvement Needs</span>
  </h1>
  <p class="family">Family Owned and Operated</p>
</section>

</body>
</html>
```